Driver License Monitoring Application Marketing Website

We need a new web design for our web application. The product is called "RoadPermitGuard." We provide a driver license monitoring service to companies and local government bodies with driver fleets. Our current website is available at www.RoadPermitGuard-example.com.

I prefer a clean, single-page design with good SEO. Attached are some PDFs with data about the project.

Target Market(s)

Companies with driver fleets, local government.

Industry/Entity Type

Government

Coding

Coded - Design and coding required

Number of Pages Required

1 page

Colors
000000

Requirements
Must have
• Content from current www.RoadPermitGuard-example.com and attached PDFs.
Nice to have
• Prefer a simple Bootstrap or similar design for easy editing.
• Room for a simple video explanation of how the product works (we don't have an actual video yet)

```html
<!DOCTYPE html>
<html lang="en">
<head>
<meta charset="utf-8">
<title>RoadPermitGuard — Florida Driver License Monitoring</title>
<link rel="stylesheet" href="https://fonts.googleapis.com/css2?family=Lato:wght@400;700&family=Cinzel:wght@400;700&family=Open+Sans:wght@400;600;700&display=swap">
<style>
:root{
  --red:#b31b22;
  --red-bright:#c8232a;
  --black:#000;
  --ink:#222;
  --cream:#ebe7d8;
  --footer:#333;
  --footer-bar:#4a4a4a;
  --white:#fff;
  --grey-line:#c9c9c9;
  --truck-green:#5aa83a;
}
*{box-sizing:border-box;margin:0;padding:0}
html,body{width:995px;height:1200px;overflow:hidden}
body{position:relative;background:var(--white);font-family:"Open Sans",sans-serif;color:var(--ink)}
.abs{position:absolute}

/* header */
.site-header{position:absolute;left:0;top:0;width:995px;height:85px;border-top:2px solid var(--red)}
.call-us{left:110px;top:13px;font-size:11px;font-weight:700}
.call-us strong{font-size:13px;font-weight:600;margin-left:3px}
.account-links{left:601px;top:0;width:123px;height:22px;background:var(--red);color:#fff;font-size:11px;display:flex;align-items:center;justify-content:space-around}
.account-links span+span{border-left:1px solid rgba(255,255,255,.35);padding-left:8px}
.search-box{left:728px;top:0;width:158px;height:22px;background:var(--red);color:#f2d3d4;font-size:11px;padding:4px 10px}
.search-box svg{position:absolute;right:6px;top:4px}
.brand{left:112px;top:44px;font-family:"Cinzel",serif;font-weight:700;font-size:25px;color:var(--black);letter-spacing:.5px}
.main-nav{top:65px;font-size:11px;font-weight:700;color:var(--black)}
.main-nav.active{color:var(--red)}

/* hero */
.hero{left:0;top:85px;width:995px;height:392px;background:var(--cream)}
.hero-art{left:80px;top:25px;width:470px;height:246px;border-radius:6px;background:linear-gradient(135deg,#7cc052,var(--truck-green) 55%,#3c7c29)}
.hero-title{right:109px;top:62px;text-align:right;font-family:"Lato",sans-serif;font-size:28px;line-height:33px;color:#333}
.hero-text{right:109px;top:143px;width:300px;text-align:right;font-family:"Lato",sans-serif;font-size:17px;line-height:19.5px;color:#333}
.btn-more{left:806px;top:238px;width:80px;height:23px;background:var(--black);color:#fff;border-radius:3px;font-size:13px;font-weight:700;text-align:center;line-height:23px;box-shadow:0 2px 2px rgba(0,0,0,.3)}
.hero-fade{left:0;top:477px;width:995px;height:70px;background:linear-gradient(#cfcfcf,#fff)}

/* features */
.features{left:109px;top:390px;width:777px;height:125px;background:#fff;border:1px solid #ddd;display:flex}
.feature{flex:1;text-align:center;padding-top:19px;position:relative}
.feature+.feature::before{content:"";position:absolute;left:0;top:8px;bottom:8px;width:10px;background:linear-gradient(90deg,rgba(0,0,0,.07),transparent)}
.feature-icon{width:49px;height:49px;border-radius:50%;background:#111;margin:0 auto;display:flex;align-items:center;justify-content:center;box-shadow:0 3px 3px rgba(0,0,0,.25)}
.feature-title{font-family:"Cinzel",serif;font-size:15px;margin-top:4px;color:#222;letter-spacing:.5px}
.feature-sub{font-size:12px;color:#333}

/* online section */
.online-title{right:545px;top:580px;text-align:right;font-family:"Cinzel",serif;font-style:italic;font-weight:700;font-size:27px;line-height:34px;color:#111}
.timeline{left:468px;top:548px}
.point{left:546px;font-family:"Lato",sans-serif;font-size:20px;color:#111}
.point.highlight{color:var(--red)}

/* bands */
.alerts{left:0;top:712px;width:497px;height:293px;background:var(--black);color:#fff;padding:26px 0 0 108px}
.benefits{left:497px;top:712px;width:498px;height:293px;background:var(--red);color:#fff;padding:26px 0 0 32px}
.band-title{font-family:"Cinzel",serif;font-weight:700;font-size:19px;margin-bottom:12px;letter-spacing:.5px}
.ticks{list-style:none;font-size:12.5px;line-height:18.6px}
.ticks>li{padding-left:24px;position:relative}
.ticks>li::before{content:"\2714";position:absolute;left:2px;top:0;font-size:13px}
.sub-list{list-style:none;font-size:11.5px;line-height:17.5px;padding-left:14px}

/* footer */
.site-footer{left:0;top:1005px;width:995px;height:155px;background:var(--footer);color:#fff;border-top:2px solid #222}
.foot-nav{top:26px;font-size:10.5px;font-weight:700}
.foot-info{font-size:10.5px;line-height:16px;letter-spacing:.4px}
.foot-info b{font-weight:700}
.inquiry-title{left:543px;top:20px;font-family:"Open Sans",sans-serif;font-size:23px}
.field{background:#fff;color:#444;font-size:10px;padding:2px 4px}
.btn-submit{left:818px;top:107px;width:68px;height:21px;background:#000;border-radius:3px;font-size:13px;font-weight:700;text-align:center;line-height:21px}
.footer-bar{left:0;top:1160px;width:995px;height:40px;background:var(--footer-bar);color:#fff}
.social{top:13px;width:16px;height:16px;border-radius:50%;background:#fff}
.copyright{right:112px;top:13px;font-size:10.5px}
</style>
</head>
<body>

<header class="site-header">
  <div class="abs call-us">Call Us: <strong>1.555.010.2740</strong></div>
  <div class="abs account-links">
    <span>&#128274; Login</span><span>&#9998; Register</span>
  </div>
  <div class="abs search-box">Search
    <svg width="12" height="12" viewBox="0 0 12 12"><circle cx="7" cy="5" r="3.8" fill="none" stroke="#fff" stroke-width="1.3"/><line x1="4.2" y1="7.8" x2="1" y2="11" stroke="#fff" stroke-width="1.5"/></svg>
  </div>
  <div class="abs brand">RoadPermitGuard</div>
  <nav>
    <span class="abs main-nav active" style="left:484px">HOME</span>
    <span class="abs main-nav" style="left:557px">LICENSE-MONITORING</span>
    <span class="abs main-nav" style="left:720px">ABOUT US</span>
    <span class="abs main-nav" style="left:815px">CONTACT US</span>
  </nav>
</header>

<section class="abs hero">
  <div class="abs hero-art" role="img" aria-label="Illustration of a green garbage collection truck"></div>
  <h1 class="abs hero-title" style="font-weight:400">Florida <b>driver license</b><br><b>monitoring</b></h1>
  <p class="abs hero-text">Monitor your fleet <b>electronically</b>. Get alerts by <b>email</b> and <b>online</b>. Never let another unlicensed or unauthorized driver behind the wheel.</p>
  <div class="abs btn-more">MORE</div>
</section>
<div class="abs hero-fade"></div>

<section class="abs features">
  <div class="feature">
    <div class="feature-icon"><svg width="18" height="24" viewBox="0 0 18 24"><circle cx="9" cy="8" r="7" fill="#fff"/><rect x="5.5" y="14" width="7" height="6" fill="#fff"/><rect x="6.5" y="21" width="5" height="2" fill="#fff"/></svg></div>
    <div class="feature-title">What We Do</div><div class="feature-sub">license monitoring</div>
  </div>
  <div class="feature">
    <div class="feature-icon"><svg width="28" height="22" viewBox="0 0 28 22"><g fill="#fff"><rect x="2" y="10" width="6" height="12"/><rect x="9" y="3" width="6" height="19"/><rect x="16" y="7" width="5" height="15"/><rect x="22" y="12" width="5" height="10"/></g></svg></div>
    <div class="feature-title">Commercial</div><div class="feature-sub">Private Sector</div>
  </div>
  <div class="feature">
    <div class="feature-icon"><svg width="26" height="24" viewBox="0 0 26 24"><g fill="#fff"><path d="M13 2a6 6 0 0 1 6 6H7a6 6 0 0 1 6-6z"/><rect x="3" y="9" width="20" height="2"/><rect x="5" y="12" width="2.5" height="8"/><rect x="10" y="12" width="2.5" height="8"/><rect x="14" y="12" width="2.5" height="8"/><rect x="19" y="12" width="2.5" height="8"/><rect x="2" y="21" width="22" height="2"/></g></svg></div>
    <div class="feature-title">Government</div><div class="feature-sub">public sector</div>
  </div>
  <div class="feature">
    <div class="feature-icon"><svg width="26" height="22" viewBox="0 0 26 22"><g fill="#fff"><circle cx="10" cy="6" r="5"/><path d="M1 21a9 7 0 0 1 18 0z"/><circle cx="18" cy="9" r="3.5"/><path d="M15 21a6 5 0 0 1 11 0z"/></g></svg></div>
    <div class="feature-title">About Us</div><div class="feature-sub">Florida law authorities</div>
  </div>
</section>

<section>
  <h2 class="abs online-title">Monitor Your<br>Whole Feet Online</h2>
  <svg class="abs timeline" width="60" height="133" viewBox="0 0 60 133">
    <line x1="29" y1="0" x2="29" y2="132" stroke="var(--grey-line)" stroke-width="1.5"/>
    <line x1="29" y1="29" x2="56" y2="29" stroke="var(--grey-line)"/><circle cx="56" cy="29" r="2.2" fill="#bbb"/>
    <line x1="0" y1="65" x2="56" y2="65" stroke="var(--grey-line)"/><circle cx="2" cy="65" r="2.2" fill="#bbb"/><circle cx="56" cy="65" r="2.2" fill="#bbb"/>
    <line x1="29" y1="101" x2="56" y2="101" stroke="var(--grey-line)"/><circle cx="56" cy="101" r="2.2" fill="#bbb"/>
  </svg>
  <div class="abs point highlight" style="top:563px">Secure</div>
  <div class="abs point" style="top:599px">Available 24 hours a day</div>
  <div class="abs point" style="top:635px;left:550px">Desktop or Mobie</div>
</section>

<section class="abs alerts">
  <h3 class="band-title">Get Instant Email Alerts</h3>
  <ul class="ticks">
    <li>Suspensions For Child Support</li>
    <li>Suspensions For Unpaid Fines</li>
    <li>Suspensions For Court Obligations</li>
    <li>Revocations For Accidents</li>
    <li>Revocations For Convictions</li>
    <li>Commercial Vehicle Disqualifications</li>
    <li>Medical Certificate Expirations</li>
    <li>License Expirations</li>
    <li>License Cancellations</li>
    <li>All Other License Sanctions</li>
  </ul>
</section>

<section class="abs benefits">
  <h3 class="band-title">Our Benefits</h3>
  <ul class="ticks">
    <li>Recive license Alerts Immediately by Email
      <ul class="sub-list">
        <li>- Suspensions</li><li>- Revocations</li><li>- Expirations</li>
        <li>- Cancellations</li><li>- Disqualifications</li><li>- Other Driver Sanctions</li>
      </ul>
    </li>
    <li>Improve Public Safety</li>
    <li>Encourage Responsible Employee Behavior</li>
    <li>Reduce Insurance Premiums</li>
    <li>Increase Productivity</li>
  </ul>
</section>

<footer class="abs site-footer">
  <span class="abs foot-nav" style="left:113px">HOME</span>
  <span class="abs foot-nav" style="left:167px">LICENSE-MONITORING</span>
  <span class="abs foot-nav" style="left:305px">ABOUT US</span>
  <span class="abs foot-nav" style="left:380px">CONTACT US</span>

  <svg class="abs" style="left:109px;top:64px" width="9" height="12" viewBox="0 0 9 12"><path d="M4.5 0a4.5 4.5 0 0 1 4.5 4.5C9 8 4.5 12 4.5 12S0 8 0 4.5A4.5 4.5 0 0 1 4.5 0z" fill="#ccc"/><circle cx="4.5" cy="4.5" r="1.6" fill="#333"/></svg>
  <div class="abs foot-info" style="left:127px;top:63px"><b>4120 Harbor<br>View Rd., Ste 210<br>Coral Springs, FL<br>33065</b></div>

  <svg class="abs" style="left:224px;top:64px" width="12" height="12" viewBox="0 0 12 12"><path d="M2 0l3 3-1.5 2a7 7 0 0 0 3.5 3.5L9 7l3 3-2 2C5 12 0 7 0 2z" fill="#ccc"/></svg>
  <div class="abs foot-info" style="left:244px;top:63px"><b>Phone:</b><br>&nbsp;1.555.010.2740</div>

  <svg class="abs" style="left:347px;top:66px" width="12" height="10" viewBox="0 0 12 10"><rect x="3" y="0" width="6" height="4" fill="#ccc"/><rect x="0" y="4" width="12" height="6" rx="1" fill="#ccc"/></svg>
  <div class="abs foot-info" style="left:367px;top:63px"><b>FAX:</b><br>(555) 010-0199</div>

  <svg class="abs" style="left:222px;top:107px" width="14" height="10" viewBox="0 0 14 10"><rect width="14" height="10" fill="#ccc"/><path d="M0 0l7 5 7-5" fill="none" stroke="#333"/></svg>
  <div class="abs foot-info" style="left:244px;top:105px"><b>Mail:</b><br>contact@roadpermitguard-example.com</div>

  <h4 class="abs inquiry-title" style="font-weight:400">Quick Inquiry</h4>
  <div class="abs field" style="left:543px;top:56px;width:174px;height:21px">Name</div>
  <div class="abs field" style="left:543px;top:81px;width:174px;height:21px">Email</div>
  <div class="abs field" style="left:543px;top:106px;width:174px;height:21px">Phone</div>
  <div class="abs field" style="left:724px;top:56px;width:162px;height:46px">Message</div>
  <div class="abs btn-submit">SUBMIT</div>
</footer>

<div class="abs footer-bar">
  <span class="abs social" style="left:112px" aria-label="Social profile"></span>
  <span class="abs social" style="left:145px" aria-label="Social profile"></span>
  <span class="abs social" style="left:177px" aria-label="Social profile"></span>
  <div class="abs copyright">© 2015 RoadPermitGuard &nbsp;|&nbsp; All Rights Reserved</div>
</div>

</body>
</html>
```